Design a compelling Tarnwove Business Card that will drive people to my site

I want a business card that I can give to people—less to tell them who I am and more to direct them to my website. My website is a portal for Pelmor Aquatics Officials and a place for people who want to become Pelmor Aquatics Officials.
I am uploading my official company logo as well as a business card mockup that I did on my own. Please feel free to completely stray from this design.
I've included a screen recording of the homepage of my website as well.
Target Market(s)
Pelmor Aquatics Officials and people who desire to become one
Contact Information for Business Card
website url
Look and feel
Each slider illustrates characteristics of the customer's brand and the style your logo design should communicate.

```html
<!DOCTYPE html>
<html lang="en">
<head>
<meta charset="utf-8">
<title>Tarnwove Business Card</title>
<link href="https://fonts.googleapis.com/css2?family=Montserrat:wght@400;500;700&display=swap" rel="stylesheet">
<style>
  :root {
    --brand-blue: #3a56a8;
    --brand-lavender: #aebbe8;
    --paper: #ffffff;
    --backdrop: #e6e7eb;
    --shadow: rgba(20, 28, 60, 0.18);
  }
  * { box-sizing: border-box; margin: 0; padding: 0; }
  html, body {
    width: 1200px; height: 912px; overflow: hidden;
    background: var(--backdrop);
    font-family: "Montserrat", Arial, sans-serif;
  }
  .sheet {
    width: 1200px; height: 912px;
    display: flex; flex-direction: column; align-items: center; justify-content: center;
    gap: 40px;
  }
  .card {
    width: 700px; height: 400px;
    border-radius: 22px;
    overflow: hidden;
    box-shadow: 0 10px 28px var(--shadow);
  }
  /* Front */
  .card-front {
    background: var(--brand-blue);
    display: flex; flex-direction: column; align-items: center; justify-content: center;
    color: var(--paper);
  }
  .brand-name {
    font-weight: 700;
    font-size: 86px;
    letter-spacing: -2px;
    line-height: 1;
  }
  .card-front .brand-name { color: var(--paper); }
  .tagline {
    margin-top: 44px;
    font-size: 21px;
    font-weight: 400;
    letter-spacing: 0.5px;
  }
  /* Back */
  .card-back { display: flex; }
  .back-logo-panel {
    width: 52%;
    background: var(--paper);
    display: flex; align-items: center; justify-content: center;
  }
  .back-logo-panel .brand-name {
    color: var(--brand-blue);
    font-size: 62px;
    letter-spacing: -1.5px;
  }
  .back-contact-panel {
    width: 48%;
    background: var(--brand-blue);
    padding: 78px 0 0 44px;
    color: var(--paper);
  }
  .person-name {
    font-weight: 700;
    font-size: 27px;
    color: var(--brand-lavender);
  }
  .person-role {
    font-size: 17px;
    margin-top: 6px;
  }
  .divider {
    width: 26px; height: 1px;
    background: var(--brand-lavender);
    margin: 16px 0 14px;
  }
  .contact-list { list-style: none; }
  .contact-item {
    display: flex; align-items: center; gap: 14px;
    font-size: 17px;
    height: 40px;
  }
  .contact-icon { width: 26px; height: 26px; flex: none; }
</style>
</head>
<body>
<main class="sheet">
  <section class="card card-front">
    <div class="brand-name">tarnwove</div>
    <p class="tagline">The Poolside Referee’s Gateway</p>
  </section>

  <section class="card card-back">
    <div class="back-logo-panel">
      <div class="brand-name">tarnwove</div>
    </div>
    <div class="back-contact-panel">
      <h1 class="person-name">Marcus Ellery</h1>
      <p class="person-role">CEO &amp; Founder</p>
      <div class="divider"></div>
      <ul class="contact-list">
        <li class="contact-item">
          <svg class="contact-icon" viewBox="0 0 26 26" aria-hidden="true">
            <circle cx="13" cy="13" r="12" fill="none" stroke="#aebbe8" stroke-width="1"/>
            <path d="M9 8.5c.6-.6 1.3-.5 1.7.1l1 1.5c.3.5.2 1-.2 1.4l-.6.5c.6 1.3 1.5 2.2 2.8 2.8l.5-.6c.4-.4.9-.5 1.4-.2l1.5 1c.6.4.7 1.1.1 1.7-1.5 1.5-4 .6-6.3-1.7S7.5 10 9 8.5z" fill="#ffffff"/>
          </svg>
          <span>(555) 201-4738</span>
        </li>
        <li class="contact-item">
          <svg class="contact-icon" viewBox="0 0 26 26" aria-hidden="true">
            <circle cx="13" cy="13" r="12" fill="none" stroke="#aebbe8" stroke-width="1"/>
            <rect x="7.5" y="9" width="11" height="8" rx="1" fill="#ffffff"/>
            <path d="M7.8 9.4L13 13.6l5.2-4.2" fill="none" stroke="#3a56a8" stroke-width="1.1"/>
          </svg>
          <span>marcus@tarnwove.com</span>
        </li>
        <li class="contact-item">
          <svg class="contact-icon" viewBox="0 0 26 26" aria-hidden="true">
            <circle cx="13" cy="13" r="12" fill="none" stroke="#aebbe8" stroke-width="1"/>
            <circle cx="13" cy="13" r="5.5" fill="none" stroke="#ffffff" stroke-width="1.2"/>
            <ellipse cx="13" cy="13" rx="2.3" ry="5.5" fill="none" stroke="#ffffff" stroke-width="1"/>
            <path d="M7.5 13h11M8.3 10.2h9.4M8.3 15.8h9.4" stroke="#ffffff" stroke-width="0.9"/>
          </svg>
          <span>www.tarnwove.com</span>
        </li>
      </ul>
    </div>
  </section>
</main>
</body>
</html>
```